Brand new letterhead, business card, email signature etc.

We are a financial company in London, UK. Our website is www.marlowvane.com. We're wanting a complete remodel of the company colours, letter head, business cards, email signatures, etc. Looking to keep the same font for the company name. I have upload a colour palette that we want to work with. We're looking for company letterhead for outgoing letters/ correspondence, letterhead for internal documentation, email signatures, e-letters. etc. Ultimately we will redesign the entire website also. It is important that our clients get a strong, secure, warm, trustworthy, solid feeling and first impression.
Updates

Designs look the same

Target Market(s)

Institutional investors, (ultra) high net worth individuals

Industry/Entity Type

Finance, Invesments banking.

Font styles to use
Other font styles liked:
• Current font is "Champagne & Limousines"

Requirements
Must have
• Must use the colours provided on the PDF uploaded to the portal. The purple = main colour. The red = accent colour.
Nice to have
• Nice to use same font as now for the company name "Corvane". Font is "Champagne & Limousines". Nice to have some reference to the old logo flower, but only subtle.
Should not have
• Do not use the colour red from our website. Use the colours provided on the colour palette PDF that I uploaded in the portal.

```html
<!DOCTYPE html>
<html lang="en">
<head>
<meta charset="utf-8">
<title>Corvane — Business Card</title>
<link rel="stylesheet" href="https://fonts.googleapis.com/css2?family=Josefin+Sans:wght@300;400&display=swap">
<style>
  :root {
    --backdrop: #7f98b9;
    --card-front: #ffffff;
    --card-back: #e6e1d7;
    --accent: #e0453a;
    --ink: #4a4446;
    --ink-soft: #6b6466;
    --line: #3a3a3a;
  }
  * { margin: 0; padding: 0; box-sizing: border-box; }
  html, body { width: 1200px; height: 876px; overflow: hidden; }
  body {
    background: var(--backdrop);
    font-family: "Josefin Sans", sans-serif;
    font-weight: 300;
    color: var(--ink);
  }
  .canvas {
    width: 1200px; height: 876px;
    display: flex; align-items: center; justify-content: center; gap: 40px;
  }
  .card {
    width: 540px; height: 310px;
    position: relative;
    box-shadow: 0 6px 18px rgba(30, 45, 70, 0.25);
  }
  .card--front { background: var(--card-front); }
  .card--back {
    background: var(--card-back);
    display: flex; flex-direction: column; align-items: center; justify-content: center; gap: 26px;
  }
  .person { position: absolute; top: 40px; left: 42px; }
  .person__name {
    color: var(--accent); font-size: 22px; font-weight: 300;
    text-transform: uppercase; letter-spacing: 0.5px;
  }
  .person__role { color: var(--ink-soft); font-size: 13px; margin-top: 4px; }
  .contacts { position: absolute; left: 42px; top: 140px; list-style: none; }
  .contacts__item {
    display: flex; align-items: flex-start; gap: 10px;
    font-size: 13px; line-height: 1.35; margin-bottom: 8px; color: var(--ink);
  }
  .contacts__icon { width: 13px; height: 13px; flex: none; margin-top: 1px; fill: var(--accent); }
  .brand { display: flex; align-items: center; gap: 12px; }
  .brand--front { position: absolute; right: 40px; bottom: 48px; }
  .brand__square { width: 30px; height: 30px; border: 1px solid var(--line); }
  .brand__name {
    font-size: 26px; font-weight: 300; letter-spacing: 8px; text-transform: uppercase; color: var(--ink);
  }
  .brand--back .brand__square { width: 56px; height: 56px; }
  .brand--back .brand__name { font-size: 34px; letter-spacing: 10px; }
  .website { display: flex; align-items: center; gap: 6px; font-size: 14px; color: var(--ink); }
  .website__icon { width: 11px; height: 11px; }
</style>
</head>
<body>
<main class="canvas">
  <section class="card card--front" aria-label="Business card front">
    <div class="person">
      <h1 class="person__name">Elias Thorne</h1>
      <p class="person__role">Director</p>
    </div>
    <ul class="contacts">
      <li class="contacts__item">
        <svg class="contacts__icon" viewBox="0 0 16 16" aria-hidden="true"><path d="M3.6 1.5l2.3 2.6-1.3 1.8c.9 2 2.5 3.6 4.5 4.5l1.8-1.3 2.6 2.3-1.4 2.2C7 15 1 9 1.4 2.9z"/></svg>
        <span>020 7946 0381</span>
      </li>
      <li class="contacts__item">
        <svg class="contacts__icon" viewBox="0 0 16 16" aria-hidden="true"><path d="M1 3h14v10H1z M1.8 3.8L8 9l6.2-5.2" fill="none" stroke="var(--accent)" stroke-width="1.6"/></svg>
        <span>info@corvane.com</span>
      </li>
      <li class="contacts__item">
        <svg class="contacts__icon" viewBox="0 0 16 16" aria-hidden="true"><path d="M8 0.8a5.4 5.4 0 0 0-5.4 5.4C2.6 10 8 15.5 8 15.5s5.4-5.5 5.4-9.3A5.4 5.4 0 0 0 8 0.8zm0 7.6a2.2 2.2 0 1 1 0-4.4 2.2 2.2 0 0 1 0 4.4z"/></svg>
        <span>Corvane Group Limited, 11th Floor<br>14 Ashby Yard, London, EC2A 9QT</span>
      </li>
    </ul>
    <div class="brand brand--front">
      <span class="brand__square" aria-hidden="true"></span>
      <span class="brand__name">Corvane</span>
    </div>
  </section>

  <section class="card card--back" aria-label="Business card back">
    <div class="brand brand--back">
      <span class="brand__square" aria-hidden="true"></span>
      <span class="brand__name">Corvane</span>
    </div>
    <p class="website">
      <svg class="website__icon" viewBox="0 0 12 12" aria-hidden="true"><circle cx="6" cy="6" r="5.5" fill="var(--ink)"/><path d="M0.5 6h11M6 0.5v11M1.5 3.5h9M1.5 8.5h9" stroke="var(--card-back)" stroke-width="0.7"/></svg>
      <span>marlowvane.com</span>
    </p>
  </section>
</main>
</body>
</html>
```